Double sided 8.5x11 Flyer

The attached text should be in the flyer. this is an election flyer for a board of director role for automotive racing industry. Try to make it exciting!

```html
<!DOCTYPE html>
<html lang="en">
<head>
<meta charset="utf-8">
<title>Daniel Corwin – Board of Directors Flyer</title>
<link href="https://fonts.googleapis.com/css2?family=Montserrat:wght@600;700;800&family=Open+Sans:wght@400;600&display=swap" rel="stylesheet">
<style>
:root{
  --teal:#1f6b73;
  --teal-dark:#154d54;
  --teal-light:#e6f0f1;
  --red:#c8202a;
  --ink:#2b2f33;
  --muted:#6b7378;
  --paper:#ffffff;
  --backdrop:#ececec;
}
*{box-sizing:border-box;margin:0;padding:0}
html,body{width:874px;height:1200px;overflow:hidden;background:var(--backdrop)}
body{position:relative;font-family:'Open Sans',sans-serif;color:var(--ink)}
.sheet{position:absolute;left:213px;width:448px;height:580px;background:var(--paper);overflow:hidden;box-shadow:0 2px 6px rgba(0,0,0,.12)}
.sheet--front{top:13px}
.sheet--back{top:607px}

/* FRONT */
.intro-panel{position:absolute;left:0;top:0;width:205px;height:300px;background:var(--teal);color:#fff;padding:18px 16px}
.stop-sign{display:block;margin:0 auto 12px}
.intro-panel__hook{font-family:'Montserrat',sans-serif;font-weight:700;font-size:11px;line-height:1.35;text-align:center}
.intro-panel__question{position:absolute;left:0;right:0;bottom:0;background:var(--teal-dark);padding:12px 12px;text-align:center}
.intro-panel__question strong{display:block;font-family:'Montserrat',sans-serif;font-size:10px;line-height:1.3;text-transform:uppercase;letter-spacing:.3px;margin-bottom:4px}
.intro-panel__question span{font-size:8px;opacity:.85}
.portrait{position:absolute;left:205px;top:0;width:243px;height:250px;background:linear-gradient(160deg,#d9dde0 0%,#9aa4ab 55%,#3e4a54 100%)}
.name-banner{position:absolute;left:205px;top:222px;width:243px;height:44px;background:var(--teal-dark);color:#fff;padding:7px 16px;text-align:right;border-left:5px solid var(--red)}
.name-banner h1{font-family:'Montserrat',sans-serif;font-weight:800;font-size:15px;letter-spacing:.6px}
.name-banner p{font-size:8px}
.keys{position:absolute;left:160px;top:318px;width:275px;list-style:none}
.key{display:flex;align-items:flex-start;gap:9px;margin-bottom:10px}
.key__icon{flex:none;width:30px;height:30px;border-radius:50%;border:2px solid var(--teal);display:flex;align-items:center;justify-content:center}
.key__label{display:inline-block;background:var(--teal);color:#fff;font-family:'Montserrat',sans-serif;font-weight:700;font-size:8px;padding:2px 10px;letter-spacing:.5px;margin-bottom:3px}
.key__text{font-size:7.5px;line-height:1.35;color:var(--muted)}
.front-aside{position:absolute;left:16px;top:322px;width:124px;font-size:7.5px;line-height:1.45;color:var(--muted)}
.front-aside b{display:block;font-family:'Montserrat',sans-serif;color:var(--teal);font-size:9px;margin-bottom:4px}
.footer{position:absolute;left:0;right:0;bottom:0;height:30px;border-top:3px solid var(--teal);display:flex;align-items:center;justify-content:space-between;padding:0 16px;font-size:7px;color:var(--muted)}
.footer__phone{font-family:'Montserrat',sans-serif;font-weight:700;font-size:10px;color:var(--teal);display:flex;align-items:center;gap:5px}

/* BACK */
.frame{position:absolute;left:12px;top:12px;right:12px;bottom:40px;border:1.5px solid var(--teal)}
.back-title{position:absolute;left:70px;top:6px;right:12px;height:24px;background:var(--teal);color:#fff;font-family:'Montserrat',sans-serif;font-weight:700;font-size:9px;display:flex;align-items:center;padding-left:18px;letter-spacing:.4px;clip-path:polygon(12px 0,100% 0,100% 100%,0 100%)}
.roles{position:absolute;left:24px;top:44px;right:24px;display:grid;grid-template-columns:1fr 1fr;column-gap:18px;row-gap:20px}
.role h3{font-family:'Montserrat',sans-serif;font-size:8px;color:var(--teal);margin-bottom:1px}
.role p{font-size:7px;line-height:1.35;color:var(--muted);border-bottom:1px solid var(--teal-light);padding-bottom:4px}
.race-photo{position:absolute;left:24px;right:24px;top:300px;height:84px;background:linear-gradient(90deg,#1a1c20 0%,#7a1016 50%,#1a1c20 100%)}
.endorse-title{position:absolute;left:0;right:0;top:392px;text-align:center;font-family:'Montserrat',sans-serif;font-weight:800;font-size:12px;color:var(--teal);letter-spacing:.5px}
.endorse-title span{color:var(--ink)}
.endorsements{position:absolute;left:24px;top:412px;width:400px;border-collapse:collapse;font-size:7px}
.endorsements th{background:var(--teal);color:#fff;font-family:'Montserrat',sans-serif;font-size:7.5px;text-align:left;padding:3px 6px}
.endorsements td{padding:3.5px 6px;border-bottom:1px solid #d5e2e4;color:var(--muted)}
.endorsements tr:nth-child(even) td{background:var(--teal-light)}
</style>
</head>
<body>

<section class="sheet sheet--front">
  <div class="intro-panel">
    <svg class="stop-sign" width="64" height="64" viewBox="0 0 64 64">
      <polygon points="19,1 45,1 63,19 63,45 45,63 19,63 1,45 1,19" fill="var(--red)" stroke="#fff" stroke-width="2"/>
      <text x="32" y="38" text-anchor="middle" font-family="Montserrat,sans-serif" font-weight="800" font-size="15" fill="#fff">STOP</text>
    </svg>
    <p class="intro-panel__hook">I need 30 seconds of your time. Just read 5 keys from Daniel before you vote.</p>
    <div class="intro-panel__question">
      <strong>How can we best serve our racing industry?</strong>
      <span>Vote Daniel Corwin for the Board of Directors</span>
    </div>
  </div>
  <div class="portrait" role="img" aria-label="Portrait photo of the candidate in a suit"></div>
  <div class="name-banner">
    <h1>DANIEL CORWIN</h1>
    <p>President, Veloxa Racing</p>
  </div>

  <div class="front-aside"><b>Why It Matters</b>Our sport needs steady hands at the top to keep tracks open and fans coming back.</div>

  <ul class="keys">
    <li class="key"><span class="key__icon"><svg width="14" height="14" viewBox="0 0 14 14"><path d="M7 1 13 13H1Z" fill="none" stroke="var(--teal)" stroke-width="1.6"/></svg></span><div><span class="key__label">PROBLEM</span><p class="key__text">Rising costs and shrinking grids threaten grassroots racing.</p></div></li>
    <li class="key"><span class="key__icon"><svg width="14" height="14" viewBox="0 0 14 14"><path d="M2 7 6 11 12 3" fill="none" stroke="var(--teal)" stroke-width="1.8"/></svg></span><div><span class="key__label">SOLUTION</span><p class="key__text">Fair rules and shared resources that keep teams on track.</p></div></li>
    <li class="key"><span class="key__icon"><svg width="14" height="14" viewBox="0 0 14 14"><path d="M3 13V1M3 2h9l-2 3 2 3H3" fill="none" stroke="var(--teal)" stroke-width="1.6"/></svg></span><div><span class="key__label">LEADERSHIP</span><p class="key__text">Twenty years guiding teams, tracks and sponsors to results.</p></div></li>
    <li class="key"><span class="key__icon"><svg width="14" height="14" viewBox="0 0 14 14"><circle cx="7" cy="7" r="5.5" fill="none" stroke="var(--teal)" stroke-width="1.6"/><path d="M7 4v3l2 2" fill="none" stroke="var(--teal)" stroke-width="1.6"/></svg></span><div><span class="key__label">EXPERIENCE</span><p class="key__text">Builder, promoter and racer who knows every side of the paddock.</p></div></li>
    <li class="key"><span class="key__icon"><svg width="14" height="14" viewBox="0 0 14 14"><path d="M1 12 5 7l3 3 5-7M10 3h3v3" fill="none" stroke="var(--teal)" stroke-width="1.6"/></svg></span><div><span class="key__label">PROGRESS</span><p class="key__text">Clear goals, open books and a board that answers to members.</p></div></li>
  </ul>

  <footer class="footer">
    <span>Paid for by the committee to elect Daniel Corwin</span>
    <span class="footer__phone"><svg width="10" height="10" viewBox="0 0 10 10"><path d="M2 1h2l1 2-1 1a5 5 0 0 0 2 2l1-1 2 1v2a1 1 0 0 1-1 1A8 8 0 0 1 1 2a1 1 0 0 1 1-1Z" fill="var(--teal)"/></svg>(555) 014-2290</span>
  </footer>
</section>

<section class="sheet sheet--back">
  <div class="frame"></div>
  <div class="back-title">THIS INDUSTRY HAS PLAYED A KEY ROLE IN MY LIFE</div>

  <div class="roles">
    <div class="role"><h3>Grassroots Karting Racer</h3><p>Started on local tracks at twelve and never looked back.</p></div>
    <div class="role"><h3>Regional Series Champion</h3><p>Won three titles while learning what teams truly need.</p></div>
    <div class="role"><h3>Crew Chief and Engineer</h3><p>Ran pit lanes and built cars for privateer programs.</p></div>
    <div class="role"><h3>Track Operations Director</h3><p>Kept events safe, on time and full of loyal fans.</p></div>
    <div class="role"><h3>Sponsor Partnership Lead</h3><p>Brought fresh funding to teams across four racing series.</p></div>
    <div class="role"><h3>Youth Program Founder</h3><p>Opened paths for young drivers and mechanics to grow.</p></div>
    <div class="role"><h3>Safety Council Member</h3><p>Helped shape modern standards now used at every event.</p></div>
    <div class="role"><h3>Team Owner and Mentor</h3><p>Built a winning shop that still trains new talent.</p></div>
    <div class="role"><h3>Industry Trade Speaker</h3><p>Shared lessons on growth at national racing conferences.</p></div>
    <div class="role"><h3>Community Event Host</h3><p>Raised support for local charities through race weekends.</p></div>
  </div>

  <div class="race-photo" role="img" aria-label="Photo of a red race car front at night"></div>

  <h2 class="endorse-title">ENDORSEMENTS <span>FROM INDUSTRY</span></h2>
  <table class="endorsements">
    <thead><tr><th>Name</th><th>Title</th><th>Quote</th></tr></thead>
    <tbody>
      <tr><td>Name Here</td><td>Team Owner</td><td>A true leader for our sport.</td></tr>
      <tr><td>Name Here</td><td>Track Director</td><td>He gets things done every time.</td></tr>
      <tr><td>Name Here</td><td>Series Promoter</td><td>The right voice for our members.</td></tr>
      <tr><td>Name Here</td><td>Race Engineer</td><td>Fair, honest and always prepared.</td></tr>
      <tr><td>Name Here</td><td>Driver Coach</td><td>He puts racers first, always.</td></tr>
    </tbody>
  </table>

  <footer class="footer">
    <span>Paid for by the committee to elect Daniel Corwin</span>
    <span class="footer__phone"><svg width="10" height="10" viewBox="0 0 10 10"><path d="M2 1h2l1 2-1 1a5 5 0 0 0 2 2l1-1 2 1v2a1 1 0 0 1-1 1A8 8 0 0 1 1 2a1 1 0 0 1 1-1Z" fill="var(--teal)"/></svg>(555) 014-2290</span>
  </footer>
</section>

</body>
</html>
```